KLV Plant Services

We are a heavy diesel mechanical business with additional air con certificates, remapping engine rebuilt

Contact Information for Business Card

Company Name, Director Name, Managing Director, Contact details, email and website

Font styles to use
Serif
Script

```html
<!DOCTYPE html>
<html lang="en">
<head>
<meta charset="utf-8">
<title>KLV Plant Services – Business Cards</title>
<link rel="stylesheet" href="https://fonts.googleapis.com/css2?family=Montserrat:wght@400;500;700;800&display=swap">
<style>
  :root {
    --backdrop: #4a4a4a;
    --card-white: #ffffff;
    --card-black: #020202;
    --brand-navy: #2b2a7a;
    --text-light: #f2f2f2;
  }
  * { box-sizing: border-box; margin: 0; padding: 0; }
  html, body { width: 1200px; height: 780px; overflow: hidden; }
  body {
    background: var(--backdrop);
    font-family: "Montserrat", sans-serif;
    position: relative;
  }
  .card {
    position: absolute;
    border-radius: 26px;
    overflow: hidden;
    background: var(--card-white);
    box-shadow: 0 14px 30px rgba(0,0,0,0.35);
  }
  /* Contact card (portrait) */
  .card--contact { left: 90px; top: 90px; width: 380px; height: 600px; }
  .card--contact .wave { position: absolute; left: 0; top: 0; width: 380px; height: 600px; }
  .brand {
    display: flex; align-items: center; gap: 12px;
    color: var(--brand-navy);
    font-weight: 800;
    white-space: nowrap;
  }
  .brand__dot {
    width: 22px; height: 22px; border-radius: 50%;
    background: var(--brand-navy); flex: none;
  }
  .card--contact .brand {
    position: absolute; left: 0; right: 0; top: 130px;
    justify-content: center; font-size: 25px;
  }
  .details {
    position: absolute; right: 34px; top: 350px;
    text-align: right; color: var(--text-light);
  }
  .details__name {
    color: var(--brand-navy); font-weight: 700; font-size: 22px;
    letter-spacing: 0.5px; text-transform: uppercase;
  }
  .details__role { font-size: 15px; margin-top: 4px; }
  .details__list { list-style: none; margin-top: 22px; font-size: 14px; }
  .details__list li {
    display: flex; justify-content: flex-end; align-items: center;
    gap: 8px; line-height: 25px;
  }
  .icon {
    width: 16px; height: 16px; border-radius: 50%;
    background: var(--brand-navy); flex: none;
    display: flex; align-items: center; justify-content: center;
  }
  .icon svg { width: 10px; height: 10px; }
  .details__address { margin-top: 14px; font-size: 14px; line-height: 22px; padding-right: 24px; }
  .accent-bar {
    position: absolute; right: 0; top: 352px;
    width: 16px; height: 126px; background: var(--brand-navy);
  }
  /* Logo card (landscape) */
  .card--logo { left: 540px; top: 210px; width: 600px; height: 360px; }
  .card--logo .brand {
    position: absolute; inset: 0; justify-content: center;
    font-size: 42px; gap: 16px;
  }
  .card--logo .brand__dot { width: 34px; height: 34px; }
</style>
</head>
<body>
  <section class="card card--contact" aria-label="Business card back with contact details">
    <svg class="wave" viewBox="0 0 380 600" aria-hidden="true">
      <path d="M0 390 C 60 300, 150 345, 250 320 C 320 300, 350 260, 380 220 L380 600 L0 600 Z" fill="var(--brand-navy)"/>
      <path d="M0 402 C 60 318, 150 360, 252 334 C 322 316, 352 276, 380 244 L380 600 L0 600 Z" fill="var(--card-black)"/>
    </svg>
    <div class="brand"><span class="brand__dot"></span>KLV Plant Services</div>
    <div class="accent-bar"></div>
    <div class="details">
      <p class="details__name">Daniel Carter</p>
      <p class="details__role">Managing Director</p>
      <ul class="details__list">
        <li>123 456 789
          <span class="icon"><svg viewBox="0 0 10 10"><path d="M2 1 L4 1 L4.6 3 L3.5 3.8 C4 5 5 6 6.2 6.5 L7 5.4 L9 6 L9 8 C5 8.5 1.5 5 2 1 Z" fill="#fff"/></svg></span></li>
        <li>info@yourmail.com
          <span class="icon"><svg viewBox="0 0 10 10"><rect x="1" y="2.5" width="8" height="5.5" fill="#fff"/><path d="M1 2.5 L5 5.5 L9 2.5" stroke="var(--brand-navy)" stroke-width="0.9" fill="none"/></svg></span></li>
        <li>www.yourwebsite.com
          <span class="icon"><svg viewBox="0 0 10 10"><circle cx="5" cy="5" r="3.8" stroke="#fff" fill="none" stroke-width="0.9"/><ellipse cx="5" cy="5" rx="1.6" ry="3.8" stroke="#fff" fill="none" stroke-width="0.8"/><path d="M1.2 5 H8.8" stroke="#fff" stroke-width="0.8"/></svg></span></li>
      </ul>
      <p class="details__address">Your address, City<br>State, Zip 1234</p>
    </div>
  </section>

  <section class="card card--logo" aria-label="Business card front">
    <div class="brand"><span class="brand__dot"></span>KLV Plant Services</div>
  </section>
</body>
</html>
```